Marlowe Ledger needs a postcard for Tax Resolutions Services

Marlowe Ledger specializes in helping taxpayers solve their problems with the QTB or state tax agencies. Whether it's back taxes, errors by other tax preparers or non paid employer taxes. We handle everything including but not limited to tax return amendments, penalty abatements, installment agreements, Injured/Innocent Spouse, Audits, Offers In Compromise, Tax Liens, and Tax Levys.

Primarily this postcard will be sent to taxpayers who have had a tax lien filed against them recently (in the past 30-90 days). We don't do hard sales, but want to urge prospects that there are ways to either lower their tax debt or get into manageable payments so that it's not so over whelming for them. Our ultimate goal is to help the taxpayers navigate this process and make it as painless for them as possible.

Target Market(s)

Typically small businesses owners and self-employed independent contractors ages 35-55 (who owe back taxes)

Industry/Entity Type

Accountant

Font styles to use
Serif
Sans Serif

Colors

Designer to choose colors to be used in the design.

Requirements
Must have
• Company logo, call to action with phone number,
• Please submit in flat format, with one side on top of the other. So that both sides can be easily seen and red. 3D views not necessary.
• Use colors from logo - Gold #C6A734, Purple: 5F1547
Nice to have
• Notification that prospects can schedule consultations online
Should not have
• No cartoony feel.
• Photos from my website

```html
<!DOCTYPE html>
<html lang="en">
<head>
<meta charset="utf-8">
<title>Marlowe Ledger – Tax Resolution Postcard</title>
<link href="https://fonts.googleapis.com/css2?family=Montserrat:wght@400;500;600;700;800&display=swap" rel="stylesheet">
<style>
  :root{
    --gold:#c6a734;
    --ink:#111111;
    --charcoal:#2b2b2b;
    --paper:#ffffff;
    --panel:#f1f1f1;
    --stage:#d9d9d9;
    --photo-denim:#5d7594;
    --photo-light:#d9dde2;
  }
  *{box-sizing:border-box;margin:0;padding:0}
  html,body{width:1200px;height:1000px;overflow:hidden}
  body{background:var(--stage);font-family:"Montserrat",Arial,sans-serif;position:relative;color:var(--ink)}

  .card{position:absolute;background:var(--paper);box-shadow:0 3px 10px rgba(0,0,0,.35);overflow:hidden}
  .card--front{left:53px;top:42px;width:690px;height:447px;background:var(--panel)}
  .card--back{left:451px;top:516px;width:690px;height:446px}
  .card svg.shapes{position:absolute;left:0;top:0}

  .brand{position:absolute;display:flex;align-items:center;gap:8px}
  .brand__mark{background:var(--gold)}
  .brand__name{font-weight:600;color:var(--gold);line-height:1;white-space:nowrap}
  .brand__tag{font-weight:500;color:var(--ink);letter-spacing:.2px;white-space:nowrap}

  .card--front .brand{left:30px;top:32px}
  .card--front .brand__mark{width:48px;height:48px}
  .card--front .brand__name{font-size:22px}
  .card--front .brand__tag{font-size:11px;margin-top:5px}

  .headline{position:absolute;left:28px;top:126px;color:var(--paper);font-weight:800;font-size:32px;line-height:34px}
  .headline__sub{position:absolute;left:30px;top:232px;color:var(--ink);font-weight:600;font-size:15.5px;line-height:19px}
  .offer{position:absolute;left:30px;top:296px;font-size:17px;line-height:20px;font-weight:500}
  .offer strong{display:block;color:var(--gold);font-weight:700}
  .callbar{position:absolute;left:0;bottom:0;width:100%;height:71px;background:var(--ink);display:flex;align-items:center;justify-content:center;gap:12px;font-weight:800;font-size:38px;color:var(--paper)}
  .callbar span{color:var(--gold)}

  .photo{position:absolute}
  .front-photo{left:0;top:0;width:690px;height:376px;clip-path:polygon(384px 0,690px 0,690px 376px,272px 376px);background:linear-gradient(135deg,var(--photo-light) 0%,#b9c0c8 35%,var(--photo-denim) 60%,#3f4f66 80%,#cfd3d8 100%)}

  .back-photo{left:0;top:0;width:385px;height:150px;background:linear-gradient(180deg,rgba(140,160,185,.9) 0%,rgba(190,200,212,.7) 55%,rgba(255,255,255,1) 100%),linear-gradient(90deg,#3d5a86 0%,#c9cfd8 60%,#ffffff 100%)}
  .question{position:absolute;left:0;width:385px;top:118px;text-align:center;font-weight:800;font-size:15px;line-height:15px}
  .question__lead{color:var(--charcoal)}
  .question__main{color:var(--gold)}
  .intro{position:absolute;left:18px;top:154px;width:338px;font-size:9.6px;line-height:12.5px;text-align:justify;color:var(--ink)}
  .intro p+p{margin-top:5px}
  .services{position:absolute;left:18px;top:226px;width:340px;display:grid;grid-template-columns:196px 1fr;row-gap:2px;list-style:none;font-size:9.6px;font-weight:700}
  .services li{display:flex;align-items:center;gap:5px}
  .services li::before{content:"";width:6px;height:6px;background:var(--gold)}

  .cta{position:absolute;left:0;top:288px;width:359px;height:118px;background:var(--ink);color:var(--paper)}
  .cta__assure{position:absolute;left:18px;top:16px;font-size:8.6px;line-height:10px;font-weight:500;padding-bottom:6px;border-bottom:1px solid var(--gold);width:240px}
  .cta__call{position:absolute;left:18px;top:50px;font-weight:800;font-size:13.5px;line-height:15px}
  .cta__call span{color:var(--gold)}
  .cta__free{position:absolute;left:18px;top:80px;font-weight:800;font-size:18px;color:var(--gold)}
  .portrait{right:6px;top:6px;width:82px;height:106px;border:1px solid #555;background:linear-gradient(180deg,#3a3a3a 0%,#6b5a52 55%,#2a2a2a 100%)}

  .email{position:absolute;left:58px;top:412px;display:flex;align-items:center;gap:6px;font-size:14px;font-weight:500}

  .card--back .brand{left:360px;top:31px}
  .card--back .brand__mark{width:36px;height:36px}
  .card--back .brand__name{font-size:15px}
  .card--back .brand__tag{font-size:8px;margin-top:3px}
  .website{position:absolute;left:398px;top:76px;font-size:12px;font-weight:700}
  .stamp{position:absolute;left:579px;top:12px;width:98px;height:98px;border:1px solid var(--ink)}
</style>
</head>
<body>

<section class="card card--front" aria-label="Postcard front">
  <div class="photo front-photo" role="img" aria-label="Stressed man resting his head on a desk beside a laptop, calculator and tax papers"></div>
  <svg class="shapes" width="690" height="447" viewBox="0 0 690 447">
    <polygon points="362,0 374,0 262,376 248,376" fill="var(--gold)"/>
    <polygon points="374,0 384,0 272,376 262,376" fill="var(--ink)"/>
    <polygon points="0,118 378,118 355,276 0,276" fill="var(--gold)"/>
    <polygon points="0,118 378,118 375,138 0,138" fill="#d4b64a" opacity=".5"/>
  </svg>
  <div class="brand">
    <div class="brand__mark"></div>
    <div>
      <div class="brand__name">MARLOWE LEDGER</div>
      <div class="brand__tag">ACCOUNTING &amp; TAX SOLUTIONS</div>
    </div>
  </div>
  <h1 class="headline">FINANCIAL<br>FREEDOM<br>FROM THE QTB</h1>
  <p class="headline__sub">WE CAN HELP RESOLVE<br>YOUR TAX PROBLEMS</p>
  <p class="offer">CALL US FOR<strong>FREE CONSULTATION</strong></p>
  <div class="callbar">CALL TODAY! <span>555-014-2938</span></div>
</section>

<section class="card card--back" aria-label="Postcard back">
  <div class="photo back-photo" role="img" aria-label="Two business people shaking hands across a desk"></div>
  <h2 class="question"><span class="question__lead">ARE YOU HAVING</span><br><span class="question__main">PROBLEMS WITH THE QTB?</span></h2>
  <div class="intro">
    <p>Marlowe Ledger in Brookfield is here to help you resolve your tax problems and put an end to the misery that the QTB can put you through. We pride ourselves on being very efficient, affordable, and, of course, extremely discrete.</p>
    <p>We can help you with the following QTB tax problems:</p>
  </div>
  <ul class="services">
    <li>Wage Garnishment</li><li>Bank Levy</li>
    <li>Threatening Letters</li><li>QTB Audit Notification</li>
    <li>Non-Filing</li><li>Liens</li>
    <li>Offers-in-Compromise</li><li>Innocent Spouse</li>
  </ul>
  <div class="cta">
    <p class="cta__assure">RESOLVE YOUR QTB TAX PROBLEM WITH THE<br>PEACE OF MIND THAT YOU ARE IN GOOD HANDS,</p>
    <p class="cta__call">CALL US AT <span>(555) 014-2938</span><br>OR CONTACT US TO SET UP A</p>
    <p class="cta__free">FREE CONSULTATION</p>
    <div class="photo portrait" role="img" aria-label="Portrait of the company's tax consultant"></div>
  </div>
  <p class="email">
    <svg width="14" height="11" viewBox="0 0 14 11" aria-hidden="true"><rect x="0.5" y="0.5" width="13" height="10" fill="var(--gold)"/><polyline points="0.5,0.5 7,6 13.5,0.5" fill="none" stroke="var(--paper)" stroke-width="1.2"/></svg>
    dana.hale@marloweledger.com
  </p>
  <div class="brand">
    <div class="brand__mark"></div>
    <div>
      <div class="brand__name">MARLOWE LEDGER</div>
      <div class="brand__tag">ACCOUNTING &amp; TAX SOLUTIONS</div>
    </div>
  </div>
  <p class="website">www.marloweledger.com</p>
  <div class="stamp" aria-label="Postage area"></div>
</section>

</body>
</html>
```